Flyer Design Project For Kitchen Rendering Service

We need an A4 Page flyer designed for a new kitchen rendering service we are launching. Our target market is other kitchen designers/manufacturers. We want them to outsource the rendering of their kitchen designs to us. Many kitchen designers still hand draw kitchens using pen and paper. This makes it hard for the end client to visualise how their new kitchen will look. Utilising specialist rendering software we transform hand drawn sketches into photographic quality renders. We provide a few different prospective renders per order giving the customer and their client a complete visualisation of the room.
Here is a few links to examples we would like to showcase.
This is the sketch our client provided: https://www.filmora-vault.net/s/qw8rtbnzx41kplm/Kitchen%20Sketch.pdf
Below is some links to the end result that we provided our client:
https://www.filmora-vault.net/s/h207xqpbnd53wr8/Kitchen%20Brochure%20Sample%2001.jpg
https://www.filmora-vault.net/s/ktaw9pmfrbx2zcy/Kitchen%20Brochure%20Sample%2003.jpg
https://www.filmora-vault.net/s/wep48nbv692hdsa/Kitchen%20Brochure%20Sample%2002.jpg
https://www.filmora-vault.net/s/gmx3rtuzp07yfkc/Kitchen%20Brochure%20Sample%2004.jpg
https://www.filmora-vault.net/s/b6nqwypa2h85jte/Kitchen%20Brochure%20Sample%2005.jpg
Our website for more info is www.hazelgrid.com.au
We only require two things from our client.
1. A drawing of any kind explaining the design (can be sketch, cad, photo, etc).
2. A completed 'Render Information From' That can be downloaded from the photographic render page of our website. http://www.hazelgrid.com.au/#!photographic-rendering/vmtb
The final design should communicate how easy it is for a kitchen designer/manufacturer to transform their basic drawings/sketchs to a photograph quality renders and help them win more jobs and boost sales using our service.
Reason: We have extended the deadline by a few days to allow us to review and provide feedback to some last minute designs that have been submitted. Thank you to all the designers that have submitted designs. Stay tuned for our feedback
Target Market(s)
Our target market is other kitchen designers/manufacturers
Industry/Entity Type
Software
Look and feel
Each slider illustrates characteristics of the customer's brand and the style your logo design should communicate.

```html
<!DOCTYPE html>
<html lang="en">
<head>
<meta charset="utf-8">
<title>Hazelgrid – Kitchen Rendering Flyer</title>
<link rel="stylesheet" href="https://fonts.googleapis.com/css2?family=Roboto:wght@300;400;700&family=Roboto+Condensed:ital,wght@1,700&display=swap">
<style>
  :root {
    --sky-deep: #8ec1dc;
    --sky-light: #f4f8fb;
    --mist: #dfe9f1;
    --ink: #1c1c1c;
    --step-blue: #1f5d9e;
    --badge-blue: #1ea2e2;
    --brand-navy: #1d3d8a;
    --footer: #5b6872;
    --footer-edge: #7b8790;
    --white: #ffffff;
  }
  * { box-sizing: border-box; margin: 0; padding: 0; }
  html, body { width: 848px; height: 1200px; overflow: hidden; background: var(--white); }
  .flyer {
    position: relative; width: 848px; height: 1200px; overflow: hidden;
    font-family: "Roboto", Arial, sans-serif; color: var(--ink);
  }
  .backdrop, .gallery { position: absolute; inset: 0; }
  .brand-seal {
    position: absolute; left: 678px; top: -42px; width: 180px; height: 180px;
    border-radius: 50%; background: var(--white);
    border-bottom: 5px solid var(--brand-navy);
    box-shadow: 0 3px 8px rgba(0,0,0,.18);
    display: flex; align-items: center; justify-content: center; padding-top: 40px;
  }
  .brand-seal__name { font-size: 22px; font-weight: 700; color: var(--brand-navy); }
  .headline {
    position: absolute; left: 52px; top: 92px;
    font-size: 70px; font-weight: 300; line-height: 84px; letter-spacing: -0.5px;
  }
  .lead {
    position: absolute; left: 52px; top: 290px;
    font-size: 24px; font-weight: 700; letter-spacing: -0.2px;
  }
  .step { position: absolute; top: 344px; }
  .step--one { left: 52px; width: 230px; }
  .step--two { left: 282px; width: 215px; }
  .step__title { font-size: 31px; font-weight: 300; color: var(--step-blue); margin-bottom: 12px; }
  .step__text { font-size: 14px; line-height: 20px; margin-bottom: 8px; }
  .offer-badge {
    position: absolute; left: 38px; top: 875px; width: 168px; height: 168px;
    border-radius: 50%; background: var(--badge-blue);
    border: 5px solid var(--white); box-shadow: 0 4px 10px rgba(0,0,0,.25);
    color: var(--white); font-family: "Roboto Condensed", "Arial Narrow", sans-serif;
    font-style: italic; font-weight: 700; text-align: center;
    transform: rotate(-12deg); padding-top: 26px; line-height: 1;
  }
  .offer-badge__big { display: block; font-size: 50px; }
  .offer-badge__small { display: block; font-size: 21px; margin-top: 4px; }
  .closing-copy {
    position: absolute; left: 374px; top: 988px; width: 450px;
    font-size: 14px; line-height: 20px;
  }
  .footer {
    position: absolute; left: 0; bottom: 0; width: 848px; height: 102px;
    background: var(--footer); border-top: 6px solid var(--footer-edge); color: var(--white);
  }
  .footer__company { position: absolute; left: 50px; top: 16px; font-size: 16px; font-weight: 700; line-height: 24px; }
  .footer__company span { display: block; font-size: 14px; }
  .footer__social { position: absolute; left: 242px; top: 52px; display: flex; gap: 12px; }
  .footer__social i { width: 26px; height: 26px; border-radius: 5px; background: var(--white); display: block; }
  .footer__call { position: absolute; right: 42px; top: 12px; text-align: right; }
  .footer__phone { font-size: 30px; font-weight: 300; }
  .footer__web { font-size: 21px; font-weight: 700; margin-top: 4px; }
</style>
</head>
<body>
<main class="flyer">
  <svg class="backdrop" width="848" height="1200" viewBox="0 0 848 1200" aria-hidden="true">
    <defs>
      <radialGradient id="skyGlow" cx="0.3" cy="0.4" r="0.8">
        <stop offset="0" stop-color="var(--sky-light)"/>
        <stop offset="1" stop-color="var(--sky-deep)"/>
      </radialGradient>
      <linearGradient id="mistFade" x1="0" y1="0" x2="0" y2="1">
        <stop offset="0" stop-color="#ffffff"/>
        <stop offset="1" stop-color="var(--mist)"/>
      </linearGradient>
    </defs>
    <rect width="848" height="1200" fill="url(#mistFade)"/>
    <path d="M0 0 H848 V600 C640 690 300 750 0 705 Z" fill="url(#skyGlow)"/>
  </svg>

  <div class="brand-seal"><span class="brand-seal__name">Hazelgrid</span></div>

  <h1 class="headline">Quality Design<br>Makes Us Different</h1>
  <p class="lead">We only require two things from our client.</p>

  <section class="step step--one">
    <h2 class="step__title">Step : 1</h2>
    <p class="step__text">A drawing of any kind explaining the design (can be sketch, cad, photo, etc).</p>
    <p class="step__text">Or A completed 'Render Information From' That can be downloaded from the photographic render page of our website. http://www.hazelgrid.com.au/#!photographic-rendering/vmtb</p>
  </section>

  <section class="step step--two">
    <h2 class="step__title">Step : 2</h2>
    <p class="step__text">We rendered Hazelgrid understands that your kitchen is the heart of your home. This is where families bond as they prepare an I need matter</p>
  </section>

  <svg class="gallery" width="848" height="1200" viewBox="0 0 848 1200">
    <defs>
      <filter id="printShadow" x="-10%" y="-10%" width="130%" height="140%">
        <feDropShadow dx="0" dy="8" stdDeviation="7" flood-color="#000" flood-opacity="0.28"/>
      </filter>
      <linearGradient id="renderBright" x1="0" y1="0" x2="1" y2="1">
        <stop offset="0" stop-color="#eef1f2"/>
        <stop offset="0.6" stop-color="#c9d0d2"/>
        <stop offset="1" stop-color="#8e9698"/>
      </linearGradient>
      <linearGradient id="renderWarm" x1="0" y1="0" x2="1" y2="1">
        <stop offset="0" stop-color="#f2f2ef"/>
        <stop offset="0.6" stop-color="#c7b49a"/>
        <stop offset="1" stop-color="#5c5a56"/>
      </linearGradient>
      <linearGradient id="renderMain" x1="0" y1="0" x2="0" y2="1">
        <stop offset="0" stop-color="#d6dadb"/>
        <stop offset="0.45" stop-color="#b9c2c0"/>
        <stop offset="1" stop-color="#5e6466"/>
      </linearGradient>
    </defs>

    <g role="img" aria-label="Kitchen render: sink and window bench" filter="url(#printShadow)" transform="rotate(-7 800 375)">
      <rect x="700" y="320" width="210" height="110" fill="#fff"/>
      <rect x="707" y="327" width="196" height="96" fill="url(#renderBright)"/>
    </g>
    <g role="img" aria-label="Kitchen render: timber benches and range hood" filter="url(#printShadow)" transform="rotate(7 740 460)">
      <rect x="585" y="395" width="310" height="135" fill="#fff"/>
      <rect x="592" y="402" width="296" height="121" fill="url(#renderWarm)"/>
    </g>
    <g role="img" aria-label="Kitchen render: wall cabinets and open shelves" filter="url(#printShadow)" transform="rotate(10 670 570)">
      <rect x="470" y="495" width="400" height="160" fill="#fff"/>
      <rect x="477" y="502" width="386" height="146" fill="url(#renderBright)"/>
    </g>
    <g role="img" aria-label="Kitchen render: island bench near window" filter="url(#printShadow)" transform="rotate(10 800 720)">
      <rect x="715" y="610" width="180" height="220" fill="#fff"/>
      <rect x="722" y="617" width="166" height="206" fill="url(#renderMain)"/>
    </g>
    <g role="img" aria-label="Kitchen render: open-plan kitchen with long island and bar stools" filter="url(#printShadow)" transform="rotate(6 505 735)">
      <rect x="250" y="578" width="510" height="315" fill="#fff"/>
      <rect x="258" y="586" width="494" height="299" fill="url(#renderMain)"/>
    </g>
  </svg>

  <div class="offer-badge">
    <span class="offer-badge__big">Free</span>
    <span class="offer-badge__small">Home design</span>
    <span class="offer-badge__small">Consultation</span>
  </div>

  <p class="closing-copy">We rendered Hazelgrid understands that your kitchen is the heart of your home. This is where families bond as they prepare an I need matter We rendered Hazelgrid understands that your kitchen is the heart of your home. This is where families bond as they</p>

  <footer class="footer">
    <p class="footer__company">Hazelgrid Pty Ltd
      <span>Elmsford, NSW 2290</span>
      <span>info@hazelgrid.com.au</span>
    </p>
    <div class="footer__social" aria-hidden="true"><i></i><i></i><i></i></div>
    <div class="footer__call">
      <p class="footer__phone">Call Now: 0400 555 018</p>
      <p class="footer__web">www.hazelgrid.com.au</p>
    </div>
  </footer>
</main>
</body>
</html>
```